Name card for fertilizer industry

We 1. produce liquid fertilizer 2. gardening supply 3. Import&Export gardening related product.
I want the name card double-sided(Chinese & English version)
detail has chinese charactor for name and address.
Target Market(s)
Farmers
Industry/Entity Type
Industry
Contact Information for Business Card
Name: Martin Kwan (鄭立朋)
TEL: +886-48-561704
FAX:+886-48-590416
MOBILE: +886-915-804-352
ADDRESS: No.87, Dongping Rd, Meiliao Township, Tainan Hsien County , TAIWAN(R.O.C) 南投縣埔里鎮東平路87號
Look and feel
Each slider illustrates characteristics of the customer's brand and the style your logo design should communicate.

```html
<!DOCTYPE html>
<html lang="en">
<head>
<meta charset="utf-8">
<title>Verdanta Enterprise Co. — Name Card</title>
<link href="https://fonts.googleapis.com/css2?family=Dosis:wght@300;400&family=Exo+2:wght@400;700&family=Noto+Sans+TC:wght@400;500&display=swap" rel="stylesheet">
<style>
  :root{
    --page:#e9e9e7;
    --card:#1d1d1d;
    --card-band:#4a4a4a;
    --muted:#8a8a8a;
    --mark:#5c5c5c;
    --green:#8cc63f;
    --green-soft:#a6d15c;
    --teal:#3fb6b0;
  }
  *{box-sizing:border-box;margin:0;padding:0}
  html,body{width:1200px;height:1000px;overflow:hidden;background:var(--page)}
  .sheet{position:relative;width:1200px;height:1000px}
  .card{position:absolute;left:240px;width:720px;height:412px;background:var(--card);overflow:hidden;box-shadow:0 6px 18px rgba(0,0,0,.18)}
  .card--front{top:60px}
  .card--back{top:530px}

  /* front */
  .brand{position:absolute;top:70px;left:0;right:0;text-align:center}
  .brand__dot{width:86px;height:86px;border-radius:50%;background:var(--mark);margin:0 auto 26px}
  .brand__name{font-family:"Dosis",sans-serif;font-weight:300;font-size:34px;letter-spacing:3px;color:var(--muted)}
  .services{position:absolute;top:250px;left:0;right:0;text-align:center;list-style:none;font-family:"Dosis",sans-serif;font-weight:300;font-size:17px;letter-spacing:1px;color:var(--muted);line-height:1.5}

  /* back */
  .band{position:absolute;inset:0}
  .person{position:absolute;right:56px;top:100px;text-align:right;font-family:"Exo 2",sans-serif}
  .person__name{font-weight:700;font-size:38px;color:var(--green)}
  .person__cjk{font-family:"Noto Sans TC",sans-serif;font-weight:400;font-size:30px;color:var(--green-soft);margin-left:6px}
  .contacts{position:absolute;right:56px;top:170px;list-style:none;font-family:"Exo 2",sans-serif;font-size:16px;color:var(--teal);line-height:1.55}
  .contacts li{display:flex;align-items:center;justify-content:flex-end;gap:10px}
  .contacts svg{width:15px;height:15px}
  .rule{position:absolute;left:40px;right:40px;top:300px;height:1px;background:var(--green)}
  .address{position:absolute;left:40px;top:316px;font-family:"Exo 2",sans-serif;color:var(--green)}
  .address__en{font-weight:700;font-size:17px}
  .address__line{font-size:16px;margin-top:6px}
  .address__line span{font-family:"Noto Sans TC",sans-serif}
</style>
</head>
<body>
<main class="sheet">
  <section class="card card--front" aria-label="Card front">
    <div class="brand">
      <div class="brand__dot"></div>
      <h1 class="brand__name">VERDANTA ENTERPRISE CO.</h1>
    </div>
    <ul class="services">
      <li>PRODUCE LIQUID FERTILIZER</li>
      <li>GARDENING SUPPLY</li>
      <li>IMPORT&amp;EXPORT GARDENING RELATED PRODUCT.</li>
    </ul>
  </section>

  <section class="card card--back" aria-label="Card back">
    <svg class="band" viewBox="0 0 720 412" preserveAspectRatio="none" aria-hidden="true">
      <path d="M430 0 C520 20 610 60 720 150 L720 0 Z" fill="var(--card-band)"/>
    </svg>
    <div class="person">
      <span class="person__name">Martin Kwan</span><span class="person__cjk">(鄭立朋)</span>
    </div>
    <ul class="contacts">
      <li>+886-48-561704
        <svg viewBox="0 0 16 16" aria-hidden="true"><path d="M4 1l3 3-2 2c1 2 3 4 5 5l2-2 3 3-2 3C7 15 1 9 1 3z" fill="var(--teal)"/></svg></li>
      <li>+886-48-590416
        <svg viewBox="0 0 16 16" aria-hidden="true"><rect x="2" y="6" width="12" height="8" fill="var(--teal)"/><rect x="4" y="2" width="8" height="5" fill="none" stroke="var(--teal)" stroke-width="1.5"/></svg></li>
      <li>+886-915-804-352
        <svg viewBox="0 0 16 16" aria-hidden="true"><rect x="4" y="1" width="8" height="14" rx="1.5" fill="none" stroke="var(--teal)" stroke-width="1.6"/></svg></li>
      <li>martin0524@mailbox.com
        <svg viewBox="0 0 16 16" aria-hidden="true"><rect x="1" y="3" width="14" height="10" fill="var(--teal)"/><path d="M1 3l7 6 7-6" fill="none" stroke="var(--card)" stroke-width="1.3"/></svg></li>
    </ul>
    <div class="rule"></div>
    <div class="address">
      <p class="address__en">No.87, Dongping Rd, Meiliao Township, Tainan Hsien County ,</p>
      <p class="address__line">TAIWAN(R.O.C) <span>南投縣埔里鎮東平路87號</span></p>
    </div>
  </section>
</main>
</body>
</html>
```